Postcard Design

We are a High intensity gym in need of a postcard that shows a possible picture of one of our coaches coaching. Corvane’s mission is to bring high intensity, results-oriented workouts to the heart of Baltimore’s Inner Harbor. This is more than just a gym – our goal is to inspire, educate, and bring fun, functional workouts to everyone! IIt doesn't have to say all of that but it does need our information and where to find us. Plus, an offer for 2 weeks free if they text the word "Perform" to 41382. Which should be the main focal point.And our website and facebook info.

Target Market(s)

Fitness, women and men ages 20-60

Industry/Entity Type

Gym

Requirements
Must have
• REMOVE DYNAVOLT FROM THE TOP OF MY LOGO

```html
<!DOCTYPE html>
<html lang="en">
<head>
<meta charset="utf-8">
<title>Corvane Performance Center Postcard</title>
<link href="https://fonts.googleapis.com/css2?family=Bebas+Neue&family=Raleway:wght@300;400;700&display=swap" rel="stylesheet">
<style>
  :root {
    --ink: #0b0b0b;
    --paper: #ffffff;
    --accent: #f2e21a;
    --photo-light: #8a8580;
    --photo-mid: #5b5651;
    --photo-dark: #2a2725;
    --logo-grey: #3a3a3a;
    --text-dark: #1a1a1a;
  }
  html, body {
    margin: 0;
    padding: 0;
    width: 1200px;
    height: 930px;
    overflow: hidden;
    background: var(--paper);
  }
  .postcard {
    position: relative;
    width: 1200px;
    height: 930px;
    background: var(--paper);
    font-family: "Raleway", Arial, sans-serif;
  }
  .promo-panel {
    position: absolute;
    left: 0;
    top: 0;
    width: 580px;
    height: 930px;
    overflow: hidden;
  }
  .coach-photo {
    position: absolute;
    inset: 0;
    background:
      radial-gradient(ellipse at 30% 45%, var(--photo-light) 0%, transparent 55%),
      linear-gradient(180deg, var(--photo-mid) 0%, var(--photo-dark) 100%);
  }
  .panel-shapes {
    position: absolute;
    inset: 0;
  }
  .wellness-heading {
    position: absolute;
    left: 135px;
    top: 42px;
    color: var(--paper);
    margin: 0;
    font-weight: 300;
    font-size: 30px;
    line-height: 36px;
  }
  .wellness-heading strong {
    display: block;
    font-weight: 700;
    font-size: 28px;
  }
  .tagline {
    position: absolute;
    right: 25px;
    top: 352px;
    margin: 0;
    text-align: right;
    font-family: "Bebas Neue", Impact, sans-serif;
    font-weight: 400;
    font-size: 96px;
    line-height: 85px;
    letter-spacing: 1px;
  }
  .tagline span { display: block; }
  .tagline .light { color: var(--paper); }
  .tagline .accent { color: var(--accent); }
  .phone {
    position: absolute;
    right: 25px;
    top: 826px;
    margin: 0;
    color: var(--paper);
    font-family: "Bebas Neue", Impact, sans-serif;
    font-size: 76px;
    line-height: 76px;
    letter-spacing: 1px;
  }
  .address {
    position: absolute;
    left: 612px;
    width: 260px;
    top: 100px;
    margin: 0;
    text-align: center;
    font-style: normal;
    color: var(--text-dark);
    font-size: 19px;
    line-height: 40px;
  }
  .brand {
    position: absolute;
    left: 920px;
    top: 45px;
    width: 225px;
    text-align: center;
  }
  .brand-mark {
    display: block;
    margin: 0 auto;
    width: 180px;
    height: 180px;
    border-radius: 50%;
    background: var(--logo-grey);
  }
  .brand-name {
    display: block;
    margin-top: 14px;
    font-weight: 700;
    font-size: 40px;
    letter-spacing: 2px;
    color: var(--logo-grey);
  }
  .offer {
    position: absolute;
    left: 610px;
    top: 340px;
    width: 560px;
    text-align: center;
    color: var(--text-dark);
  }
  .offer-kicker {
    margin: 0;
    font-family: "Bebas Neue", Impact, sans-serif;
    font-size: 44px;
    line-height: 48px;
    letter-spacing: 2px;
  }
  .offer-headline {
    margin: 0;
    font-family: "Bebas Neue", Impact, sans-serif;
    font-weight: 400;
    font-size: 120px;
    line-height: 116px;
    color: var(--ink);
  }
  .offer-action {
    display: inline-block;
    margin: 12px 0 0;
    padding: 10px 28px;
    background: var(--ink);
    color: var(--paper);
    font-family: "Bebas Neue", Impact, sans-serif;
    font-size: 50px;
    line-height: 56px;
    letter-spacing: 1px;
  }
  .offer-action em {
    font-style: normal;
    color: var(--accent);
  }
  .online {
    position: absolute;
    left: 610px;
    top: 760px;
    width: 560px;
    margin: 0;
    text-align: center;
    color: var(--text-dark);
    font-size: 21px;
    line-height: 40px;
  }
  .online strong { font-weight: 700; }
</style>
</head>
<body>
  <main class="postcard">
    <section class="promo-panel">
      <div class="coach-photo" role="img" aria-label="Photo of a coach leading a group workout with training poles in a gym"></div>
      <svg class="panel-shapes" width="580" height="930" viewBox="0 0 580 930" aria-hidden="true">
        <polygon points="142,36 580,36 580,136 90,136" fill="var(--ink)"/>
        <polygon points="112,802 580,802 580,930 0,930 0,870 84,870" fill="var(--ink)"/>
        <polyline points="580,802 112,802 84,870 0,870" fill="none" stroke="var(--accent)" stroke-width="5"/>
      </svg>
      <h2 class="wellness-heading">Ask us about our <strong>Corporate Wellness Programs</strong></h2>
      <p class="tagline">
        <span class="light">Fun</span>
        <span class="accent">Educational</span>
        <span class="light">Motivating</span>
        <span class="accent">Workouts</span>
      </p>
      <p class="phone">717-555-0148</p>
    </section>

    <address class="address">
      Corvane Performance Center<br>
      418 E. Calder St. Suite 400<br>
      Baltimore, MD. 21202
    </address>

    <div class="brand">
      <span class="brand-mark" aria-hidden="true"></span>
      <span class="brand-name">CORVANE</span>
    </div>

    <section class="offer">
      <p class="offer-kicker">Try us out &mdash; on the house</p>
      <h1 class="offer-headline">2 Weeks Free</h1>
      <p class="offer-action">Text <em>&ldquo;Perform&rdquo;</em> to <em>41382</em></p>
    </section>

    <p class="online">
      <strong>Web:</strong> corvaneperformance.com<br>
      <strong>Facebook:</strong> facebook.com/corvanebaltimore
    </p>
  </main>
</body>
</html>
```